Consulting company business cards

We have a base design, but would be willing to update. We have a new logo/"tag" that needs to be added. Current business card design is attached for reference into our "style."

Industry/Entity Type

Business

Contact Information for Business Card

Should contain name and title, office number, mobile number if appropriate, e-mail, website, physical address, and company logo.

Font styles to use
Other font styles liked:
• See current card design on KorvandBCard

Colors
0455a3
85acd3
aaaaaa

Requirements
Must have
• Our colors are navy blue, gray, and a lighter blue
Nice to have
• Design that I can easily drop in new names/titles as we hire employees.

```html
<!DOCTYPE html>
<html lang="en">
<head>
<meta charset="utf-8">
<title>Wrenfield Business Card</title>
<link rel="stylesheet" href="https://fonts.googleapis.com/css2?family=PT+Sans:wght@400;700&display=swap">
<style>
  :root {
    --stage: #000000;
    --navy: #05304f;
    --navy-text: #0a3556;
    --light-blue: #85acd3;
    --card-gray: #d3d3d3;
    --tag-gray: #9a9a9a;
    --white: #ffffff;
  }
  html, body {
    margin: 0;
    padding: 0;
    width: 1200px;
    height: 900px;
    overflow: hidden;
    background: var(--stage);
    font-family: "PT Sans", Arial, sans-serif;
  }
  .stage {
    position: relative;
    width: 1200px;
    height: 900px;
  }
  .card {
    position: absolute;
    top: 275px;
    width: 477px;
    height: 294px;
    overflow: hidden;
  }
  .card-front {
    left: 116px;
    background: var(--navy);
    border-radius: 0 56px 0 56px;
    color: var(--white);
    text-align: center;
  }
  .card-back {
    left: 622px;
    background: var(--card-gray);
    border-radius: 56px 0 56px 0;
  }
  .brand-name {
    position: absolute;
    font-weight: 400;
    font-size: 50px;
    line-height: 1;
    letter-spacing: 0.5px;
  }
  .card-front .brand-name {
    top: 30px;
    left: 0;
    right: 0;
    color: var(--white);
  }
  .card-back .brand-name {
    top: 36px;
    left: 40px;
    color: var(--navy-text);
  }
  .tagline {
    position: absolute;
    font-size: 11.5px;
    letter-spacing: 1.6px;
    line-height: 1;
  }
  .card-front .tagline {
    top: 89px;
    left: 0;
    right: 0;
    color: #dfe8f0;
  }
  .card-back .tagline {
    top: 93px;
    left: 42px;
    color: var(--tag-gray);
  }
  .person-name {
    position: absolute;
    top: 131px;
    left: 0;
    right: 0;
    font-weight: 700;
    font-size: 19px;
    line-height: 1;
  }
  .person-title {
    position: absolute;
    top: 155px;
    left: 0;
    right: 0;
    font-size: 14px;
    line-height: 1;
  }
  .divider {
    position: absolute;
    top: 180px;
    left: 0;
    width: 100%;
    height: 1px;
    background: var(--light-blue);
  }
  .contact {
    position: absolute;
    left: 0;
    right: 0;
    font-size: 14px;
    line-height: 1;
  }
  .contact-address { top: 194px; }
  .contact-phones { top: 220px; word-spacing: 2px; }
  .contact-web { top: 240px; }
  .sep { margin: 0 12px; }
  .contact-web .sep { margin: 0 4px; }
  .mascot-area {
    position: absolute;
    left: 195px;
    top: 112px;
    width: 282px;
    height: 182px;
    border-radius: 120px 0 56px 0;
    background: linear-gradient(160deg, #f4f4f4 0%, #ffffff 55%, #ececec 100%);
  }
</style>
</head>
<body>
  <main class="stage">
    <section class="card card-front">
      <div class="brand-name">Wrenfield</div>
      <div class="tagline">A CLOUD CONSULTING COMPANY</div>
      <div class="person-name">Dana Korvand</div>
      <div class="person-title">Office Manager</div>
      <div class="divider"></div>
      <div class="contact contact-address">1850 N Birchwood Ave Carmel Indiana 46032</div>
      <div class="contact contact-phones">317.555.0148<span class="sep">|</span>317.555.0193</div>
      <div class="contact contact-web">dkorvand@wrenfieldcloud.com<span class="sep">|</span>wrenfieldcloud.com</div>
    </section>

    <section class="card card-back">
      <div class="brand-name">Wrenfield</div>
      <div class="tagline">A CLOUD CONSULTING COMPANY</div>
      <div class="mascot-area" role="img" aria-label="Large white illustration of the company's animal mascot in profile"></div>
    </section>
  </main>
</body>
</html>
```